Pinecrest Harbor Foundation Web Design

The design we need is for a WordPress blog that will be our content platform. We are a registered 501(c)3 non-profit that focuses on financially supporting the treatment of cancer patients that have been told they have no hope and there is nothing the conventional medical system can do for them. Through this wesbite we want to both rasie awareness about the treatment options plus, raise funds for treating patients. The two primary target audiences of the site are...

1. Terminally ill patients and their families to let them know that there is an option other then hospice and that we are hear to support that option.

2. People looking to help donate to a worthwhile cause that resonates with them.

The website is https://pinecrestharborfoundation.org/

See attached logo designs!!!

Target Market(s)

Cancer patients and their families

Industry/Entity Type

Foundation

Font styles to use
Sans Serif

Colors
ffffff
fbed22

Requirements
Must have
• I like this look of this site. It is clean, simple, helpful, soft. I like the flow of the pages.
• http://www.meadowsforcalm.org/
• I like the design and flow but NOT the color or boldness
• https://tvbn-youth.org/
• I like this style for a donation page.
• https://www.tumorstudyhub.org/we-are-tsh/join-the-cause/donations/one-time-donation
• with the addition of a Would you like your employer to match? button.
Nice to have
• White black and gold - but soft
• Even possibly grayscale like the site I like.

```html
<!DOCTYPE html>
<html lang="en">
<head>
<meta charset="utf-8">
<title>Pinecrest Harbor Foundation</title>
<link href="https://fonts.googleapis.com/css2?family=Roboto:wght@400;500;700;900&family=Open+Sans:wght@400;600&display=swap" rel="stylesheet">
<style>
:root{
  --gold:#e2c547;
  --gold-soft:#f3e49a;
  --gold-deep:#b8962a;
  --charcoal:#3a3a3a;
  --charcoal-dark:#2c2c2c;
  --charcoal-deep:#222222;
  --ink:#2d2d2d;
  --muted:#7a7a7a;
  --line:#e4e4e4;
  --soft:#f4f4f2;
  --white:#ffffff;
}
*{box-sizing:border-box;margin:0;padding:0}
html,body{width:1200px;height:2796px;overflow:hidden;background:var(--white)}
body{position:relative;font-family:"Open Sans",Arial,sans-serif;color:var(--ink);font-size:14px;line-height:1.6}
h1,h2,h3,h4,.nav a,.btn{font-family:"Roboto",Arial,sans-serif}
section,header,nav,footer{position:absolute;left:0;width:1200px}

/* header */
.site-header{top:0;height:136px}
.brand{position:absolute;left:100px;top:36px;display:flex;align-items:center;gap:14px}
.brand-mark{width:58px;height:58px;border-radius:50%;background:var(--gold)}
.brand-name{font-family:"Roboto",sans-serif;font-weight:700;font-size:34px;color:var(--charcoal);line-height:1.05}
.brand-sub{display:block;font-size:13px;font-weight:700;letter-spacing:1.5px;text-transform:uppercase;color:var(--charcoal);margin-top:4px}
.call{position:absolute;left:700px;top:44px;display:flex;align-items:center;gap:14px}
.call-icon{width:46px;height:46px;border-radius:50%;border:2px solid var(--gold-deep);display:flex;align-items:center;justify-content:center}
.call-label{font-family:"Roboto",sans-serif;font-size:15px;font-weight:500;color:var(--muted);line-height:1.2}
.call-number{font-family:"Roboto",sans-serif;font-size:20px;font-weight:700;color:var(--ink);line-height:1.2}
.btn{display:inline-block;font-weight:700;font-size:14px;text-transform:uppercase;letter-spacing:.5px;text-decoration:none}
.btn-gold{background:var(--gold);color:var(--charcoal-deep)}
.btn-dark{background:var(--charcoal);color:var(--white)}
.header-donate{position:absolute;left:940px;top:46px;padding:13px 26px}

/* nav */
.nav{top:136px;height:42px;background:var(--charcoal);display:flex;justify-content:center}
.nav a{color:var(--white);font-size:13px;font-weight:500;text-transform:uppercase;padding:0 22px;line-height:42px;text-decoration:none}
.nav a.active{background:var(--gold);color:var(--charcoal-deep)}

/* hero */
.hero{top:178px;height:462px;overflow:hidden}
.hero-photo{position:absolute;inset:0;background:linear-gradient(180deg,#9aa0a4 0%,#c4c7c8 45%,#8b9093 62%,#cdbfa6 85%,#b9a585 100%)}
.hero-text{position:absolute;left:100px;top:188px}
.hero-text h1{font-size:40px;font-weight:900;color:var(--white);line-height:1.1;text-transform:uppercase}
.hero-text .btn{margin-top:18px;padding:9px 20px;font-size:13px}
.slider-arrows{position:absolute;left:100px;top:404px;display:flex;gap:12px}

/* welcome */
.welcome{top:640px;height:500px}
.video-thumb{position:absolute;left:210px;top:110px;width:372px;height:296px;background:linear-gradient(135deg,#d9b9a8,#c59f8a 50%,#a09488)}
.play{position:absolute;left:156px;top:118px;width:60px;height:60px;border-radius:50%;background:rgba(255,255,255,.9);display:flex;align-items:center;justify-content:center}
.welcome-copy{position:absolute;left:640px;top:108px;width:420px}
.welcome-copy h2{font-size:26px;font-weight:700;line-height:1.25;text-transform:uppercase;margin-bottom:20px}
.welcome-copy p{font-size:12px;color:var(--muted);line-height:1.7;margin-bottom:12px}
.welcome-copy .btn{margin-top:14px;padding:8px 18px;font-size:12px}

/* what we do */
.services{top:1140px;height:540px;background:linear-gradient(180deg,#f7f7f6 0%,#ececea 45%,#c9c9c6 75%,#e6e6e4 100%)}
.section-title{text-align:center;font-size:34px;font-weight:700;text-transform:uppercase;padding-top:48px}
.title-rule{width:60px;height:3px;background:var(--gold);margin:12px auto 0}
.service-cards{position:absolute;left:210px;top:180px;display:flex;gap:44px}
.service-card{width:234px;height:214px;background:var(--white);text-align:center;padding:0 18px;position:relative;box-shadow:0 2px 10px rgba(0,0,0,.08)}
.service-icon{width:74px;height:74px;border-radius:50%;background:var(--gold);border:5px solid var(--white);margin:-30px auto 10px;display:flex;align-items:center;justify-content:center}
.service-card h3{font-size:18px;font-weight:500;margin-bottom:8px}
.service-card p{font-size:11px;color:var(--muted);line-height:1.6}
.read-link{display:inline-block;margin-top:10px;font-family:"Roboto",sans-serif;font-size:11px;border:1px solid #999;border-radius:12px;padding:2px 12px;color:var(--ink)}

/* blog */
.blog{top:1680px;height:520px}
.blog .section-title{padding-top:60px}
.blog-cards{position:absolute;left:210px;top:190px;display:flex;gap:30px}
.blog-card{width:250px}
.blog-photo{position:relative;height:186px}
.blog-photo.p1{background:linear-gradient(135deg,#6e5e52,#b09a86)}
.blog-photo.p2{background:linear-gradient(135deg,#c4c6c8,#b8a58a 60%,#e9e4dc)}
.blog-photo.p3{background:linear-gradient(135deg,#b8bec4,#7c8794 60%,#dcdfe2)}
.date-badge{position:absolute;left:12px;top:0;width:46px;height:52px;background:var(--gold);color:var(--charcoal-deep);text-align:center;font-family:"Roboto",sans-serif;line-height:1.1;padding-top:8px}
.date-badge b{display:block;font-size:18px}
.date-badge span{font-size:11px}
.blog-card h4{font-size:15px;font-weight:700;margin:14px 0 6px}
.blog-card p{font-size:11px;color:var(--muted);line-height:1.6}

/* testimonial */
.testimonial{top:2200px;height:250px}
.quote{position:absolute;left:130px;top:46px;width:760px}
.quote p{font-size:13px;color:var(--muted);font-style:italic;line-height:1.7}
.quote cite{display:block;margin-top:14px;font-style:normal;font-family:"Roboto",sans-serif;font-size:13px;color:var(--gold-deep);font-weight:500}
.avatar{position:absolute;left:940px;top:30px;width:150px;height:150px;border-radius:50%;background:radial-gradient(circle at 50% 40%,#cbb7a4,#9a9c9e 70%);border:5px solid var(--white);box-shadow:0 0 0 2px var(--line)}

/* footer */
.site-footer{top:2410px;height:386px}
.footer-wave{position:absolute;left:0;top:0}
.footer-body{position:absolute;left:0;top:40px;width:1200px;height:310px;background:var(--charcoal-dark)}
.footer-cols{position:absolute;left:100px;top:40px;display:flex;color:var(--white)}
.footer-col h4{font-size:14px;font-weight:700;text-transform:uppercase;margin-bottom:16px;color:var(--gold)}
.footer-col{font-size:12px;line-height:1.7}
.col-contact{width:330px}
.col-signup{width:320px}
.col-links{width:200px}
.col-social{width:200px}
.contact-row{display:flex;gap:10px;margin-bottom:10px;align-items:flex-start}
.contact-row svg{flex:none;margin-top:3px}
.email-input{width:250px;height:32px;background:var(--white);margin:12px 0}
.footer-col .btn{padding:7px 16px;font-size:12px}
.quick-links a{display:block;color:var(--white);text-decoration:none;line-height:1.75}
.social-row{display:flex;align-items:center;gap:10px;margin-bottom:8px}
.social-dot{width:24px;height:24px;border-radius:50%;border:1px solid rgba(255,255,255,.7)}
.copyright{position:absolute;left:0;top:350px;width:1200px;height:36px;background:var(--charcoal-deep);color:var(--white);text-align:center;font-size:11px;line-height:36px}
</style>
</head>
<body>

<header class="site-header">
  <div class="brand">
    <span class="brand-mark"></span>
    <span class="brand-name">Pinecrest Harbor<span class="brand-sub">Foundation</span></span>
  </div>
  <div class="call">
    <span class="call-icon">
      <svg width="20" height="20" viewBox="0 0 24 24"><path d="M6.6 10.8c1.4 2.8 3.8 5.1 6.6 6.6l2.2-2.2c.3-.3.7-.4 1-.2 1.1.4 2.3.6 3.6.6.6 0 1 .4 1 1V20c0 .6-.4 1-1 1C10.6 21 3 13.4 3 4c0-.6.4-1 1-1h3.5c.6 0 1 .4 1 1 0 1.3.2 2.5.6 3.6.1.3 0 .7-.2 1l-2.3 2.2z" fill="#b8962a"/></svg>
    </span>
    <div>
      <div class="call-label">CALL US</div>
      <div class="call-number">+1 555 014 2290</div>
    </div>
  </div>
  <a class="btn btn-gold header-donate">Donate Now</a>
</header>

<nav class="nav">
  <a class="active">Home</a>
  <a>About Pinecrest Harbor Foundation</a>
  <a>Services</a>
  <a>Our Vision</a>
  <a>Donate</a>
  <a>Blog</a>
  <a>Contact Us</a>
</nav>

<section class="hero">
  <div class="hero-photo" role="img" aria-label="Woman with open arms standing on a beach at the sea shore"></div>
  <div class="hero-text">
    <h1>Pinecrest<br>Harbor<br>Foundation</h1>
    <a class="btn btn-gold">Get Involved</a>
  </div>
  <div class="slider-arrows">
    <svg width="14" height="18" viewBox="0 0 14 18"><path d="M11 2 4 9l7 7" stroke="#fff" stroke-width="3" fill="none"/></svg>
    <svg width="14" height="18" viewBox="0 0 14 18"><path d="M3 2l7 7-7 7" stroke="#fff" stroke-width="3" fill="none"/></svg>
  </div>
</section>

<section class="welcome">
  <div class="video-thumb" role="img" aria-label="Group of women in pink shirts at a cancer support walk">
    <span class="play"><svg width="22" height="24" viewBox="0 0 22 24"><path d="M3 2l17 10L3 22z" fill="#b8962a"/></svg></span>
  </div>
  <div class="welcome-copy">
    <h2>Welcome to<br>Pinecrest Harbor Foundation</h2>
    <p>Sed ut perspiciatis unde omnis iste natus error sit voluptatem accusantium doloremque laudantium, totam rem aperiam, eaque ipsa quae ab illo inventore veritatis et quasi architecto beatae vitae dicta sunt explicabo. Nemo enim ipsam voluptatem quia voluptas sit aspernatur aut odit aut fugit.</p>
    <p>Neque porro quisquam est, qui dolorem ipsum quia dolor sit amet, consectetur, adipisci velit, sed quia non numquam eius modi tempora incidunt ut labore et dolore magnam aliquam quaerat voluptatem.</p>
    <a class="btn btn-dark">Read More</a>
  </div>
</section>

<section class="services" aria-label="What we do">
  <h2 class="section-title">What We Do</h2>
  <div class="title-rule"></div>
  <div class="service-cards">
    <div class="service-card">
      <div class="service-icon"><svg width="30" height="30"><circle cx="15" cy="15" r="10" fill="none" stroke="#fff" stroke-width="3"/></svg></div>
      <h3>Quis autem vel eum iure</h3>
      <p>Sed ut perspiciatis unde omnis iste natus error sit voluptatem accusantium doloremque laudantium, totam rem aperiam eaque ipsa quae ab illo inventore.</p>
    </div>
    <div class="service-card">
      <div class="service-icon"><svg width="30" height="30"><circle cx="15" cy="15" r="10" fill="none" stroke="#fff" stroke-width="3"/></svg></div>
      <h3>Cancer Patients</h3>
      <p>Sed ut perspiciatis unde omnis iste natus error sit voluptatem accusantium doloremque laudantium, totam rem aperiam eaque ipsa.</p>
      <span class="read-link">Read more</span>
    </div>
    <div class="service-card">
      <div class="service-icon"><svg width="30" height="30"><circle cx="15" cy="15" r="10" fill="none" stroke="#fff" stroke-width="3"/></svg></div>
      <h3>Quis autem vel eum iure</h3>
      <p>Sed ut perspiciatis unde omnis iste natus error sit voluptatem accusantium doloremque laudantium, totam rem aperiam eaque ipsa quae ab illo inventore.</p>
    </div>
  </div>
</section>

<section class="blog" aria-label="Latest blog">
  <h2 class="section-title">Latest Blog</h2>
  <div class="blog-cards">
    <article class="blog-card">
      <div class="blog-photo p1" role="img" aria-label="Two people sharing a quiet moment together"><div class="date-badge"><b>02</b><span>JAN</span></div></div>
      <h4>Lorem ipsum dolor sit amet,</h4>
      <p>Sed ut perspiciatis unde omnis iste natus error sit voluptatem accusantium doloremque laudantium, totam rem aperiam.</p>
    </article>
    <article class="blog-card">
      <div class="blog-photo p2" role="img" aria-label="Volunteers holding a large fundraising banner"><div class="date-badge"><b>02</b><span>JAN</span></div></div>
      <h4>Lorem ipsum dolor sit amet,</h4>
      <p>Sed ut perspiciatis unde omnis iste natus error sit voluptatem accusantium doloremque laudantium, totam rem aperiam.</p>
    </article>
    <article class="blog-card">
      <div class="blog-photo p3" role="img" aria-label="Team of supporters in matching shirts outdoors"><div class="date-badge"><b>02</b><span>JAN</span></div></div>
      <h4>Lorem ipsum dolor sit amet,</h4>
      <p>Sed ut perspiciatis unde omnis iste natus error sit voluptatem accusantium doloremque laudantium, totam rem aperiam.</p>
    </article>
  </div>
</section>

<section class="testimonial" aria-label="Testimonial">
  <blockquote class="quote">
    <p>&ldquo;Sed ut perspiciatis unde omnis iste natus error sit voluptatem accusantium doloremque laudantium, totam rem aperiam, eaque ipsa quae ab illo inventore veritatis et quasi architecto beatae vitae dicta sunt explicabo. Nemo enim ipsam voluptatem quia voluptas sit aspernatur aut odit aut fugit, sed quia consequuntur magni dolores eos qui ratione.</p>
    <cite>John Doe - Pinecrest Harbor Foundation</cite>
  </blockquote>
  <div class="avatar" role="img" aria-label="Portrait of the quoted supporter"></div>
</section>

<footer class="site-footer">
  <svg class="footer-wave" width="1200" height="60" viewBox="0 0 1200 60" preserveAspectRatio="none"><path d="M0 40 Q600 -10 1200 40 L1200 60 L0 60Z" fill="#2c2c2c"/></svg>
  <div class="footer-body">
    <div class="footer-cols">
      <div class="footer-col col-contact">
        <h4>Contact Us</h4>
        <div class="contact-row">
          <svg width="12" height="16" viewBox="0 0 12 16"><path d="M6 0a6 6 0 0 0-6 6c0 4.5 6 10 6 10s6-5.5 6-10a6 6 0 0 0-6-6zm0 8.5A2.5 2.5 0 1 1 6 3.5a2.5 2.5 0 0 1 0 5z" fill="#fff"/></svg>
          <span>Pinecrest Harbor Foundation<br>2140 Cedar Lane, Harbor Bay</span>
        </div>
        <div class="contact-row">
          <svg width="14" height="14" viewBox="0 0 24 24"><path d="M6.6 10.8c1.4 2.8 3.8 5.1 6.6 6.6l2.2-2.2c.3-.3.7-.4 1-.2 1.1.4 2.3.6 3.6.6.6 0 1 .4 1 1V20c0 .6-.4 1-1 1C10.6 21 3 13.4 3 4c0-.6.4-1 1-1h3.5c.6 0 1 .4 1 1 0 1.3.2 2.5.6 3.6.1.3 0 .7-.2 1l-2.3 2.2z" fill="#fff"/></svg>
          <span>Phone : +1 555 014 2290</span>
        </div>
        <div class="contact-row">
          <svg width="14" height="12" viewBox="0 0 14 12"><rect x=".5" y=".5" width="13" height="11" fill="none" stroke="#fff"/><path d="M.5 .5 7 6.5 13.5 .5" fill="none" stroke="#fff"/></svg>
          <span>info@pinecrestharborfoundation.org</span>
        </div>
      </div>
      <div class="footer-col col-signup">
        <h4>Sign Up to Receive Email</h4>
        <p>Updates and occasional news from our team, sent a few times each season to your inbox.</p>
        <div class="email-input"></div>
        <a class="btn btn-gold">Subscribe</a>
      </div>
      <div class="footer-col col-links">
        <h4>Quick Links</h4>
        <div class="quick-links">
          <a>Home</a><a>About Us</a><a>Services</a><a>Our Vision</a><a>Donate</a><a>Blog</a><a>Contact Us</a>
        </div>
      </div>
      <div class="footer-col col-social">
        <h4>Social Media</h4>
        <div class="social-row"><span class="social-dot"></span>Facepage</div>
        <div class="social-row"><span class="social-dot"></span>Chirper</div>
        <div class="social-row"><span class="social-dot"></span>Searchly+</div>
        <div class="social-row"><span class="social-dot"></span>Viewtube</div>
      </div>
    </div>
  </div>
  <div class="copyright">Copyright &copy; Pinecrest Harbor Foundation 2017. All rights reserved.</div>
</footer>

</body>
</html>
```